Web Design Project

i'm looking for a sleek modern design i can use for a web site that deals with.
Intelligent Data Capture
Accounts Payable Solutions for faster processing based on our scanning solution.
ultimately we are a intelligent scanning software.

here is a great website, that does exactly what we do, and we like to have most of their services and products.

so something in this idea would be great.
www.valtrino.com

so i guess i want a good landing/home page which is smartly designed so users will be inclined to leave their information.

and then information pages.

also i dont need any cms for you to include, i only need you to hook the html hooks for RANK Kettle as i already have a CMS and need it to hook in to that, i am including links to that cheat sheet.
so it is easier when included as you create the Theme.

http://www.rankkettle.com/how-to-create-website-template.html
http://www.rankkettle.com/cheat-sheet.html
Updates

Hi Guys sorry for the long pause in design, but here is where we stand.

what ever design i choose, i need that designer to customize a few things for me based on design that was designed.
and i will need designer to match that them to work with RANK Kettle
here is the cheat sheet for the hooks that we need to match and make it work.
if you have any questions let me know.

otherwise i look forward to working with you. and good luck.

Target Market(s)

CFO's AP Managers, mostly ppl who are not Tech freindly

Industry/Entity Type

Software

Requirements
Must have
• i need on home page, the rotating banner should have 1 ability to place youtube links to show videos, and also ability to add buttons on these rotating banners that will allow forms to pop up take to another page.

```html
<!DOCTYPE html>
<html lang="en">
<head>
<meta charset="utf-8">
<title>Lumen – Home</title>
<link rel="stylesheet" href="https://fonts.googleapis.com/css2?family=PT+Sans:ital,wght@0,400;0,700;1,400;1,700&family=Source+Sans+3:wght@300;400;600&display=swap">
<style>
  :root {
    --orange: #f08a1c;
    --orange-deep: #e8771a;
    --orange-light: #f7a33c;
    --ink: #2f2f2f;
    --grey-text: #5a5a5a;
    --nav-grey: #5f5f66;
    --band: #efefef;
    --white: #ffffff;
  }
  * { margin: 0; padding: 0; box-sizing: border-box; }
  html, body { width: 1200px; height: 1200px; overflow: hidden; background: var(--white); }
  body { position: relative; font-family: "Source Sans 3", sans-serif; color: var(--grey-text); }

  .logo { position: absolute; left: 132px; top: 14px; font-family: "Source Sans 3", sans-serif; font-weight: 400; font-size: 42px; color: var(--orange); letter-spacing: 0.5px; }

  .search { position: absolute; left: 928px; top: 0; width: 141px; height: 24px; background: linear-gradient(#f8a948, var(--orange-deep)); border-radius: 0 0 10px 10px; font-family: "PT Sans", sans-serif; font-style: italic; font-size: 13px; color: var(--white); padding: 4px 0 0 14px; }
  .search svg { position: absolute; right: 8px; top: 3px; }

  .main-nav { position: absolute; top: 36px; left: 549px; display: flex; gap: 31px; font-family: "PT Sans", sans-serif; font-style: italic; font-weight: 700; font-size: 16px; }
  .main-nav a { color: var(--nav-grey); text-decoration: none; height: 28px; line-height: 28px; }
  .main-nav a.active { background: linear-gradient(#f8a948, var(--orange-deep)); color: var(--white); border-radius: 8px; padding: 0 17px; margin-right: -17px; }

  .hero { position: absolute; left: 100px; top: 80px; width: 1000px; height: 400px; }
  .hero-photo { position: absolute; inset: 0; }
  .hero-caption { position: absolute; left: 62px; top: 95px; width: 517px; height: 203px; background: rgba(150,140,135,0.45); border: 1px solid rgba(120,110,105,0.8); }
  .hero-title { position: absolute; left: 15px; top: 6px; font-family: "PT Sans", sans-serif; font-style: italic; font-weight: 700; font-size: 34px; color: #2a2623; white-space: nowrap; }
  .hero-sub { position: absolute; left: 15px; top: 47px; font-family: "PT Sans", sans-serif; font-style: italic; font-weight: 700; font-size: 21px; color: #2a2623; }
  .hero-text { position: absolute; left: 16px; top: 83px; width: 440px; font-family: "PT Sans", sans-serif; font-style: italic; font-size: 13px; line-height: 17px; color: #2a2623; }
  .btn-learn { position: absolute; left: 18px; top: 144px; width: 142px; height: 39px; border-radius: 8px; background: linear-gradient(#f9ad4a, var(--orange-deep)); box-shadow: 0 4px 6px rgba(0,0,0,0.35); font-family: "PT Sans", sans-serif; font-style: italic; font-weight: 700; font-size: 19px; color: var(--white); text-align: center; line-height: 39px; }
  .slider-dots { position: absolute; left: 883px; top: 343px; display: flex; gap: 9px; }
  .slider-dots span { width: 12px; height: 12px; border-radius: 50%; background: #3a3532; }
  .slider-dots span.on { background: var(--orange); }

  .about-title { position: absolute; left: 119px; top: 498px; font-family: "PT Sans", sans-serif; font-style: italic; font-weight: 400; font-size: 20px; color: #4a4f5a; }
  .body-copy { position: absolute; left: 119px; width: 636px; font-size: 12.5px; line-height: 24px; text-align: justify; color: #666; }
  .copy-1 { top: 529px; }
  .copy-2 { top: 680px; }
  .copy-3 { top: 866px; }
  .subheading { position: absolute; left: 119px; top: 832px; font-family: "PT Sans", sans-serif; font-style: italic; font-weight: 400; font-size: 18px; color: var(--orange); }
  .read-more { position: absolute; left: 670px; top: 936px; font-family: "PT Sans", sans-serif; font-style: italic; font-weight: 700; font-size: 13px; color: var(--orange-deep); }
  .about-photo { position: absolute; left: 770px; top: 535px; width: 293px; height: 153px; border: 2px solid #dcdcdc; border-radius: 6px; padding: 3px; background: var(--white); box-shadow: 0 1px 3px rgba(0,0,0,0.15); }
  .about-photo div { width: 100%; height: 100%; border-radius: 3px; background: radial-gradient(circle at 50% 60%, #ffffff, #cfe4f5 55%, #a9cbe8); }

  .partners { position: absolute; left: 100px; top: 982px; width: 1000px; height: 140px; background: linear-gradient(#f5f5f5, #e9e9e9); }
  .partners-title { position: absolute; left: 50px; top: 44px; font-size: 29px; color: #4e4640; }
  .partners-sub { position: absolute; left: 51px; top: 76px; font-size: 16px; color: #4e4640; }
  .partner { position: absolute; top: 52px; font-family: "Source Sans 3", sans-serif; font-weight: 600; font-size: 30px; color: #9a9a9a; }
  .partner-next { position: absolute; left: 890px; top: 62px; }

  .footer { position: absolute; left: 100px; top: 1122px; width: 1000px; height: 78px; background: var(--orange-deep); box-shadow: inset 0 3px 4px -2px rgba(100,50,0,0.6); }
  .footer-nav { position: absolute; left: 38px; top: 29px; display: flex; gap: 31px; font-family: "PT Sans", sans-serif; font-style: italic; font-size: 17px; color: var(--white); }
  .follow { position: absolute; left: 758px; top: 24px; display: flex; align-items: center; gap: 9px; font-family: "PT Sans", sans-serif; font-style: italic; font-weight: 700; font-size: 14px; color: var(--white); }
  .follow i { display: inline-block; width: 20px; height: 20px; border-radius: 50%; background: rgba(255,255,255,0.85); }
  .copyright { position: absolute; left: 758px; top: 52px; font-family: "PT Sans", sans-serif; font-style: italic; font-weight: 700; font-size: 13px; color: var(--white); }
</style>
</head>
<body>

<header>
  <div class="logo">Lumen</div>
  <div class="search">Search
    <svg width="20" height="18" viewBox="0 0 20 18"><circle cx="8" cy="7" r="5" fill="none" stroke="#fff" stroke-width="2"/><line x1="12" y1="11" x2="18" y2="16" stroke="#fff" stroke-width="3" stroke-linecap="round"/></svg>
  </div>
  <nav class="main-nav">
    <a class="active">Home</a><a>About us</a><a>Services</a><a>Testimonials</a><a>Blog</a><a>Contact</a>
  </nav>
</header>

<section class="hero">
  <svg class="hero-photo" width="1000" height="400" viewBox="0 0 1000 400" role="img" aria-label="Photo of a person reading a document on a smartphone over an open magazine">
    <defs>
      <linearGradient id="heroTone" x1="0" y1="0" x2="1" y2="0.3">
        <stop offset="0" stop-color="#4a3a33"/>
        <stop offset="0.35" stop-color="#9a7e6c"/>
        <stop offset="0.65" stop-color="#cbb8a8"/>
        <stop offset="1" stop-color="#8c5a3c"/>
      </linearGradient>
    </defs>
    <rect width="1000" height="400" fill="url(#heroTone)"/>
    <path d="M0 0 L0 8 Q2 18 14 20 Q500 28 986 20 Q998 18 1000 8 L1000 0 Z" fill="#fff"/>
    <path d="M0 400 L0 392 Q4 380 20 378 Q500 340 980 378 Q996 380 1000 392 L1000 400 Z" fill="#fff"/>
  </svg>
  <div class="hero-caption">
    <div class="hero-title">Sed ut perspiciatis unde omnis</div>
    <div class="hero-sub">Miste natus error sit</div>
    <p class="hero-text">Sed ut perspiciatis unde omnis iste natus error sit voluptatem accusantium doloremque laudantium, totam rem aperiam, eaque ipsa quae ab illo inventore veritatis</p>
    <div class="btn-learn">Learn More</div>
  </div>
  <div class="slider-dots"><span class="on"></span><span></span><span></span><span></span></div>
</section>

<main>
  <h2 class="about-title">ABOUT US</h2>
  <p class="body-copy copy-1">Sed ut perspiciatis unde omnis iste natus error sit voluptatem accusantium doloremque laudantium, totam rem aperiam, eaque ipsa quae ab illo inventore veritatis et quasi architecto beatae vitae dicta sunt explicabo. Nemo enim ipsam consequunturSed ut perspiciatis unde omnis iste natus error sit voluptatem accusantium doloremque laudantium, totam rem aperiam, eaque ipsa quae ab illo inventore veritatis et quasi architecto beatae vitae dicta sunt explicabo. Nemo enim ipsam consequunturSed ut perspiciatis unde omnis iste natus error sit voluptatem accusantium doloremque laudantium, totam rem aperiam,</p>
  <p class="body-copy copy-2">Sed ut perspiciatis unde omnis iste natus error sit voluptatem accusantium doloremque laudantium, totam rem aperiam, eaque ipsa quae ab illo inventore veritatis et quasi architecto beatae vitae dicta sunt explicabo. Nemo enim ipsam consequunturSed ut perspiciatis unde omnis iste natus error sit voluptatem accusantium doloremque laudantium, totam rem aperiam, eaque ipsa quae ab illo inventore veritatis et quasi architecto beatae vitae dicta sunt explicabo. Nemo enim ipsam consequunturSed ut perspiciatis unde omnis iste natus error sit voluptatem accusantium doloremque laudantium, totam rem aperiam,</p>
  <h3 class="subheading">Subheading</h3>
  <p class="body-copy copy-3">Sed ut perspiciatis unde omnis iste natus error sit voluptatem accusantium doloremque laudantium, totam rem aperiam, eaque ipsa quae ab illo inventore veritatis et quasi architecto beatae vitae dicta sunt explicabo. Nemo enim ipsam consequunturSed ut perspiciatis unde omnis iste natus</p>
  <a class="read-more">Read more...</a>
  <figure class="about-photo"><div role="img" aria-label="Photo of a businesswoman at a desk surrounded by floating video-call windows"></div></figure>
</main>

<section class="partners">
  <div class="partners-title">Partners</div>
  <div class="partners-sub">We carry a wide selection of Partners</div>
  <span class="partner" style="left:322px">Corvane</span>
  <span class="partner" style="left:458px">Halden</span>
  <span class="partner" style="left:618px">Brightwell</span>
  <span class="partner" style="left:768px">Marisol</span>
  <svg class="partner-next" width="22" height="28" viewBox="0 0 22 28"><path d="M5 3 L16 14 L5 25" fill="none" stroke="#b5b5b5" stroke-width="5"/></svg>
</section>

<footer class="footer">
  <nav class="footer-nav"><span>Home</span><span>About us</span><span>Services</span><span>Testimonials</span><span>Blog</span><span>Contact</span></nav>
  <div class="follow">Follow us : <i></i><i></i><i></i><i></i><i></i></div>
  <div class="copyright">© 2012. www.lumenscan.com</div>
</footer>

</body>
</html>
```